Dusty Spur Outfitters Home Page

I need a logo and page design for my home page, maybe some background color suggestions to go with it. I want the logo to project "vintage" and "western wear" but not be your typical trite western saddle and gun type thing.
http://www.dustyspuroutfitters.example/store/cart.php
Not looking for page coding just logo and other design elements to lay in over the site's template to make it "pop"
Reason: Have to finalize the design.
Target Market(s)
My customers are 70/30 men to women.
Industry/Entity Type
Gun

```html
<!DOCTYPE html>
<html lang="en">
<head>
<meta charset="utf-8">
<title>Dusty Spur Outfitters — Header Colour Options</title>
<link rel="stylesheet" href="https://fonts.googleapis.com/css2?family=Lato:wght@700;900&family=Norican&display=swap">
<style>
  :root {
    --canvas-beige: #cdb99b;
    --canvas-beige-light: #d6c4a7;
    --teal: #3f8f98;
    --teal-dark: #357f88;
    --body-charcoal: #201f1e;
    --body-slate: #29393a;
    --body-navy: #212a31;
    --cream: #e8dcc2;
    --tagline: #d9ccb0;
    --search-text: #2e2a25;
    --shadow: rgba(0, 0, 0, 0.35);
  }

  * { margin: 0; padding: 0; box-sizing: border-box; }

  html, body {
    width: 1200px;
    height: 1000px;
    overflow: hidden;
  }

  body {
    position: relative;
    background:
      repeating-linear-gradient(45deg, rgba(255,255,255,0.04) 0 2px, rgba(0,0,0,0.03) 2px 4px),
      linear-gradient(180deg, var(--canvas-beige-light), var(--canvas-beige));
    font-family: "Lato", Arial, sans-serif;
  }

  .header-option {
    position: absolute;
    left: 0;
    width: 1200px;
    height: 164px;
    box-shadow: 0 3px 4px var(--shadow);
  }
  .header-option--charcoal { top: 147px; --body: var(--body-charcoal); }
  .header-option--slate    { top: 416px; --body: var(--body-slate); height: 166px; }
  .header-option--navy     { top: 691px; --body: var(--body-navy); height: 166px; }

  .header-option__band {
    position: absolute;
    left: 0;
    width: 100%;
    height: 17px;
    background: linear-gradient(180deg, var(--teal), var(--teal-dark));
  }
  .header-option__band--top { top: 0; }
  .header-option__band--bottom { bottom: 0; }

  .header-option__body {
    position: absolute;
    left: 0;
    top: 17px;
    bottom: 17px;
    width: 100%;
    background:
      radial-gradient(ellipse at 30% 40%, rgba(255,255,255,0.05), transparent 60%),
      radial-gradient(ellipse at 80% 70%, rgba(255,255,255,0.04), transparent 55%),
      var(--body);
    border-bottom: 3px solid rgba(0,0,0,0.45);
  }

  .brand {
    position: absolute;
    left: 60px;
    top: 56px;
    display: flex;
    align-items: center;
    gap: 14px;
    color: var(--cream);
    font-weight: 900;
    font-size: 34px;
    letter-spacing: 0.5px;
    white-space: nowrap;
  }
  .brand__dot {
    width: 34px;
    height: 34px;
    border-radius: 50%;
    background: var(--cream);
    flex: none;
  }

  .tagline {
    position: absolute;
    left: 476px;
    top: 84px;
    font-family: "Norican", cursive;
    font-size: 25px;
    color: var(--tagline);
    white-space: nowrap;
  }

  .search {
    position: absolute;
    left: 901px;
    top: 51px;
    display: flex;
    align-items: center;
    gap: 11px;
  }
  .search__field {
    width: 173px;
    height: 30px;
    border-radius: 15px;
    background: var(--cream);
    color: var(--search-text);
    font-weight: 700;
    font-size: 17px;
    line-height: 30px;
    padding-left: 17px;
  }
  .search__button {
    color: var(--tagline);
    font-weight: 700;
    font-size: 18px;
  }
</style>
</head>
<body>

  <section class="header-option header-option--charcoal" aria-label="Header option, charcoal">
    <div class="header-option__band header-option__band--top"></div>
    <div class="header-option__body"></div>
    <div class="header-option__band header-option__band--bottom"></div>
    <div class="brand"><span class="brand__dot"></span>Dusty Spur Outfitters</div>
    <p class="tagline">Brand-New Retro Styled Western Wear</p>
    <div class="search"><span class="search__field">Search...</span><span class="search__button">GO!</span></div>
  </section>

  <section class="header-option header-option--slate" aria-label="Header option, slate">
    <div class="header-option__band header-option__band--top"></div>
    <div class="header-option__body"></div>
    <div class="header-option__band header-option__band--bottom"></div>
    <div class="brand"><span class="brand__dot"></span>Dusty Spur Outfitters</div>
    <p class="tagline">Brand-New Retro Styled Western Wear</p>
    <div class="search"><span class="search__field">Search...</span><span class="search__button">GO!</span></div>
  </section>

  <section class="header-option header-option--navy" aria-label="Header option, navy">
    <div class="header-option__band header-option__band--top"></div>
    <div class="header-option__body"></div>
    <div class="header-option__band header-option__band--bottom"></div>
    <div class="brand"><span class="brand__dot"></span>Dusty Spur Outfitters</div>
    <p class="tagline">Brand-New Retro Styled Western Wear</p>
    <div class="search"><span class="search__field">Search...</span><span class="search__button">GO!</span></div>
  </section>

</body>
</html>
```